Mobile welding fabrication and repair, heavy equipment and semi repair

We need a business card design that will catch the eye but look prelesional at the same time. Were based out of Idaho and we do all welding fabrication jobs and repairs, we also build and install custom pipe fences for personal or larger scale fence jobs and can give free quotes. We can do semi truck and trailer repairs Mobily also.

Target Market(s)

Welding

Industry/Entity Type

welding and repair

Contact Information for Business Card

email (ravenforgeandmend@mailbay.net, phone number 208-417-3826, owner (Dalton Whitcomb), Pipe Fence, Semi Repair, Mobile welding and fabrication

Font styles to use
Sans Serif

Requirements
Must have
• My logo in black background on one side , and other side my logo in white back round with all the information listed on card details
Nice to have
• make it stand out from other business cards

```html
<!DOCTYPE html>
<html lang="en">
<head>
<meta charset="UTF-8">
<title>Raven Forge and Mend – Business Card</title>
<link href="https://fonts.googleapis.com/css2?family=Arimo:ital,wght@0,400;0,700;1,400&display=swap" rel="stylesheet">
<style>
  :root {
    --page: #ffffff;
    --card-front: #ffffff;
    --card-back: #000000;
    --brand-blue: #1668c2;
    --ink: #231f20;
    --muted: #8a8a8a;
    --service-gray: #6d6d6d;
    --rule: #9a9a9a;
    --band-start: #58aee2;
    --band-mid: #6396cf;
    --band-end: #1a55b1;
  }
  * { margin: 0; padding: 0; box-sizing: border-box; }
  html, body {
    width: 1200px; height: 1200px; overflow: hidden;
    background: var(--page);
    font-family: "Arimo", Arial, sans-serif;
  }
  .canvas { position: relative; width: 1200px; height: 1200px; }
  .card {
    position: absolute; left: 294px; width: 612px; height: 382px; overflow: hidden;
  }
  .card--front {
    top: 205px; background: var(--card-front);
    box-shadow: 0 0 3px rgba(0,0,0,0.25);
  }
  .card--back { top: 612px; background: var(--card-back); }

  .wordmark {
    font-weight: 700; color: var(--brand-blue);
    text-transform: uppercase; letter-spacing: 1px; line-height: 1.05;
  }
  .card--front .wordmark {
    position: absolute; left: 44px; top: 38px; font-size: 38px;
  }
  .card--back .wordmark {
    position: absolute; left: 0; right: 0; top: 132px;
    text-align: center; font-size: 50px;
  }

  .services {
    position: absolute; left: 42px; top: 274px;
    list-style: none; font-style: italic; color: var(--service-gray);
    font-size: 17px; line-height: 17.5px;
  }
  .divider {
    position: absolute; left: 190px; top: 276px; width: 1px; height: 65px;
    background: var(--rule);
  }
  .contact {
    position: absolute; right: 42px; top: 233px; text-align: right; color: var(--ink);
  }
  .contact__name { font-size: 29px; font-weight: 700; letter-spacing: 0.3px; line-height: 1.1; }
  .contact__role { font-size: 19px; color: var(--muted); margin-top: 1px; }
  .contact__lines { margin-top: 13px; font-size: 18px; line-height: 20px; }
  .contact__line { display: flex; justify-content: flex-end; align-items: center; gap: 7px; }
  .contact__line svg { width: 14px; height: 16px; flex: none; }

  .accent-band {
    position: absolute; left: 0; right: 0; bottom: 0; height: 16px;
    background: linear-gradient(90deg, var(--band-start), var(--band-mid) 55%, var(--band-end));
  }
</style>
</head>
<body>
<main class="canvas">
  <section class="card card--front" aria-label="Card front">
    <div class="wordmark">Raven Forge<br>and Mend</div>

    <ul class="services">
      <li>Pipe Fence</li>
      <li>Semi Repair</li>
      <li>Mobile Welding</li>
      <li>Fabrication</li>
    </ul>
    <div class="divider"></div>

    <div class="contact">
      <div class="contact__name">DALTON WHITCOMB</div>
      <div class="contact__role">Owner</div>
      <div class="contact__lines">
        <div class="contact__line">
          <span>208-417-3826</span>
          <svg viewBox="0 0 14 16" aria-hidden="true">
            <rect x="3" y="1" width="8" height="14" rx="1.5" fill="none" stroke="var(--brand-blue)" stroke-width="1.6"/>
            <circle cx="7" cy="12.5" r="0.9" fill="var(--brand-blue)"/>
          </svg>
        </div>
        <div class="contact__line">
          <span>ravenforgeandmend@mailbay.net</span>
          <svg viewBox="0 0 14 16" aria-hidden="true">
            <path d="M1 7 L7 2.5 L13 7 V14 H1 Z" fill="var(--brand-blue)"/>
            <path d="M1 7 L7 11 L13 7 M1 14 L5.5 10 M13 14 L8.5 10" fill="none" stroke="#fff" stroke-width="1"/>
          </svg>
        </div>
      </div>
    </div>

    <div class="accent-band"></div>
  </section>

  <section class="card card--back" aria-label="Card back">
    <div class="wordmark">Raven Forge<br>and Mend</div>
  </section>
</main>
</body>
</html>
```